Indy Film Production Company/Studio

We need a business card designed from an existing logo. We are a digital studio/production company that caters to creating genre entertainment, like Action, Horror, and martial arts. The card along with the logo will be used to Brand the company from letter heads to banners. The design will also be used for postcards and Brochures. It should be professional and masculine.
Updates

Thank you to all the designers who have participated. I'm narrowing down who it will be. Thank you again.

Target Market(s)

Investors, Networks, Producers, and actors

Industry/Entity Type

Film Production

Contact Information for Business Card

Teodoro Valbuena
Producer/Writer/Director
www.kestrelpicturehouse.example

Requirements
Must have
• Website address, Facebook icon and Twitter icon possibly in the back of the card.
Nice to have
• Logline of Company: Follow The Action.

```html
<!DOCTYPE html>
<html lang="en">
<head>
<meta charset="utf-8">
<title>Kestrel Picturehouse – Business Card</title>
<link rel="stylesheet" href="https://fonts.googleapis.com/css2?family=Open+Sans:wght@400;700;800&display=swap">
<style>
  :root {
    --stage: #3a2f2b;
    --card-front: #f6f6f4;
    --card-back: #151515;
    --ink: #111111;
    --ink-soft: #2a2a2a;
    --paper: #f2f2f2;
  }
  * { box-sizing: border-box; margin: 0; padding: 0; }
  html, body {
    width: 1200px;
    height: 844px;
    overflow: hidden;
    background: var(--stage);
  }
  .stage {
    position: relative;
    width: 1200px;
    height: 844px;
    display: flex;
    align-items: center;
    justify-content: center;
    gap: 60px;
  }
  .card {
    position: relative;
    width: 504px;
    height: 288px;
    border-radius: 3px;
    box-shadow: 0 14px 30px rgba(0,0,0,0.45);
    font-family: "Open Sans", Arial, sans-serif;
  }
  .card--front { background: var(--card-front); color: var(--ink); }
  .card--back  { background: var(--card-back); color: var(--paper); }

  .wordmark {
    position: absolute;
    display: flex;
    align-items: center;
    gap: 8px;
    font-weight: 800;
    text-transform: uppercase;
    letter-spacing: 0.04em;
    line-height: 1;
  }
  .wordmark__mark {
    width: 12px;
    height: 12px;
    background: currentColor;
  }
  .card--front .wordmark {
    top: 52px;
    right: 48px;
    font-size: 20px;
    color: var(--ink);
  }
  .card--back .wordmark {
    top: 50%;
    left: 50%;
    transform: translate(-50%, -50%);
    font-size: 24px;
    color: var(--paper);
  }

  .contact {
    position: absolute;
    left: 40px;
    bottom: 34px;
    color: var(--ink-soft);
    font-size: 13px;
    line-height: 1.45;
  }
  .contact__name {
    font-weight: 700;
    font-size: 15px;
    color: var(--ink);
  }
  .contact__role { margin-bottom: 16px; }
  .contact__address { margin-bottom: 16px; }
</style>
</head>
<body>
  <main class="stage">
    <section class="card card--front" aria-label="Business card, front">
      <div class="wordmark">
        <span class="wordmark__mark" aria-hidden="true"></span>
        <span class="wordmark__name">Kestrel Picturehouse</span>
      </div>
      <div class="contact">
        <p class="contact__name">John Smith</p>
        <p class="contact__role">Managing Director</p>
        <p class="contact__address">1234, Address GoesHere, Country, 12345</p>
        <p class="contact__lines">T:(044) 123 456 789 &nbsp;F:(044) 123456789 &nbsp;M:(044)123456789</p>
        <p class="contact__lines">E:info@youremail.com &nbsp;&nbsp;www.yourweb.com</p>
      </div>
    </section>

    <section class="card card--back" aria-label="Business card, back">
      <div class="wordmark">
        <span class="wordmark__mark" aria-hidden="true"></span>
        <span class="wordmark__name">Kestrel Picturehouse</span>
      </div>
    </section>
  </main>
</body>
</html>
```